Business Card For Halvenmoor Financial Consulting

Hi, I would like a business card designed. Bold, modern.
Please use the same design as the logo. I have also attached the website design to see the overall theme.
Wordmark Font
Color: Hex: #01AEF7

```html
<!DOCTYPE html>
<html lang="en">
<head>
<meta charset="utf-8">
<title>Halvenmoor Financial Consulting – Business Card</title>
<link rel="stylesheet" href="https://fonts.googleapis.com/css2?family=Montserrat:wght@400;600;700&display=swap">
<style>
  :root {
    --bg: #7d7d7b;
    --paper: #fbfbfb;
    --navy: #0d3a68;
    --navy-deep: #16212c;
    --sky: #01aef7;
    --sky-mid: #2f93d6;
    --ink: #2b2f36;
    --rule: #8fa3b5;
  }
  * { margin: 0; padding: 0; box-sizing: border-box; }
  html, body { width: 1200px; height: 801px; overflow: hidden; }
  body {
    background: var(--bg);
    font-family: "Montserrat", Arial, sans-serif;
    position: relative;
  }
  .card {
    position: absolute;
    top: 250px;
    width: 520px;
    height: 300px;
    overflow: hidden;
    box-shadow: 0 10px 24px rgba(0,0,0,.28);
  }
  .card--front { left: 40px; background: var(--paper); border-bottom: 3px solid var(--sky); }
  .card--back { left: 640px; background: var(--navy-deep); border-bottom: 3px solid var(--sky); }

  .wave { position: absolute; inset: 0; width: 100%; height: 100%; }

  .brand {
    position: absolute;
    left: 30px;
    top: 66px;
    display: flex;
    align-items: center;
    gap: 10px;
  }
  .brand__mark { width: 26px; height: 26px; border: 3px solid var(--sky-mid); flex: none; }
  .brand__name {
    font-weight: 700;
    font-size: 17px;
    line-height: 1.15;
    letter-spacing: .06em;
    text-transform: uppercase;
    color: var(--navy);
    width: 150px;
  }

  .divider {
    position: absolute;
    left: 222px;
    top: 32px;
    width: 1.5px;
    height: 122px;
    background: var(--rule);
  }

  .contact {
    position: absolute;
    left: 240px;
    top: 28px;
    color: var(--ink);
    font-size: 12px;
    line-height: 1.45;
  }
  .contact__name { font-weight: 700; font-size: 17px; line-height: 1.3; color: var(--navy); text-transform: uppercase; letter-spacing: .01em; }
  .contact__title { color: var(--sky-mid); font-size: 13px; margin-bottom: 8px; }
  .contact__address { margin-bottom: 8px; }
  .contact__line { display: flex; align-items: center; gap: 6px; }
  .contact__line svg { width: 11px; height: 11px; flex: none; }

  .card__url {
    position: absolute;
    right: 22px;
    bottom: 26px;
    color: #fff;
    font-size: 13px;
    letter-spacing: .01em;
  }

  .back-brand {
    position: absolute;
    left: 50%;
    top: 50%;
    transform: translate(-50%, -50%);
    display: flex;
    align-items: center;
    gap: 16px;
  }
  .back-brand__mark { width: 44px; height: 44px; border: 4px solid var(--sky-mid); flex: none; }
  .back-brand__name {
    font-weight: 700;
    font-size: 26px;
    line-height: 1.15;
    letter-spacing: .08em;
    text-transform: uppercase;
    color: #fff;
    width: 270px;
  }
</style>
</head>
<body>

  <section class="card card--front" aria-label="Business card front">
    <svg class="wave" viewBox="0 0 520 300" preserveAspectRatio="none" aria-hidden="true">
      <path d="M0,272 C180,270 300,255 380,205 C430,174 470,160 520,156 L520,300 L0,300 Z" fill="var(--sky-mid)"/>
      <path d="M0,280 C184,278 308,264 388,214 C438,183 476,170 520,166 L520,300 L0,300 Z" fill="#ffffff"/>
      <path d="M0,283 C186,281 311,267 391,217 C441,186 478,173 520,169 L520,300 L0,300 Z" fill="var(--navy)"/>
    </svg>

    <div class="brand">
      <span class="brand__mark"></span>
      <span class="brand__name">Halvenmoor Financial Consulting</span>
    </div>

    <div class="divider"></div>

    <div class="contact">
      <p class="contact__name">Marek Olsten</p>
      <p class="contact__title">President</p>
      <p class="contact__address">18430 Cove Ridge Drive<br>Laguna Vista CA 92710</p>
      <p class="contact__line">
        <svg viewBox="0 0 24 24" aria-hidden="true"><path fill="var(--sky-mid)" d="M6.6 10.8a15 15 0 0 0 6.6 6.6l2.2-2.2a1 1 0 0 1 1-.25 11.4 11.4 0 0 0 3.6.57 1 1 0 0 1 1 1V20a1 1 0 0 1-1 1A17 17 0 0 1 3 4a1 1 0 0 1 1-1h3.5a1 1 0 0 1 1 1c0 1.25.2 2.45.57 3.57a1 1 0 0 1-.25 1z"/></svg>
        555-240-6817
      </p>
      <p class="contact__line">
        <svg viewBox="0 0 24 24" aria-hidden="true"><path fill="var(--navy)" d="M2 5h20v14H2z"/><path fill="none" stroke="#fff" stroke-width="2" d="M2 6l10 7 10-7"/></svg>
        info@HalvenmoorConsulting.com
      </p>
    </div>

    <p class="card__url">HalvenmoorConsulting.com</p>
  </section>

  <section class="card card--back" aria-label="Business card back">
    <div class="back-brand">
      <span class="back-brand__mark"></span>
      <span class="back-brand__name">Halvenmoor Financial Consulting</span>
    </div>
  </section>

</body>
</html>
```